Product Description page for Hullwrap.com, References here just need a clean up redesign

Hi, were working on updating the product description page of our site hullwrap.com

Attached is a reference of what we drew on paint. We want to keep it pretty much the same as far as whats on there, the components with a few small adjustments and a clean actually designed look.

1. We want to remove the tabs (product description, warranty, reviews) and put it all in that main content area stretching down into sections. IE: Product Description section, followed by reviews, followed by warranty, below each other.
2. The side bar needs to be redesigned as far as the look and feel but the content and whats in there should stay the same.
3. The main banner area will be replaced shortly you do not have to worry about that.
4. Include a section or box for people to put in their email for a free Ebook.

Target Market(s)

people looking to easily view our boat cover products and buy without having to click too often or leave the page.

Industry/Entity Type

Online Shopping

Number of Pages Required

1 page

Requirements
Must have
• - Must update the sidebar
• - Must update the content area to remove the tabs and put the content from each tab sectioned off below each other (dummy text is fine for now for the tabs you cant view)
Nice to have
• - Cool place thats clean and functional to insert a section for people to put in their email to receive a free ebook
Should not have
• - too much change, we already know what we want and have a solid reference to work from.

```html
<!DOCTYPE html>
<html lang="en">
<head>
<meta charset="utf-8">
<title>Hullwrap.com – Boat Cover up to 16'8" Long and 90" Wide</title>
<link href="https://fonts.googleapis.com/css2?family=Oswald:wght@500;600&family=Open+Sans:wght@400;600;700&family=Roboto:wght@400;500;700&family=Noto+Sans:wght@400&display=swap" rel="stylesheet">
<style>
:root{
  --blue-dark:#0a2a9c;
  --blue:#1340c9;
  --blue-link:#1a3fc2;
  --red:#e0241b;
  --orange:#f7955a;
  --ink:#222;
  --muted:#555;
  --line:#c9c9c9;
  --panel-bg:#f3fbfc;
  --field:#e2e2e2;
}
*{box-sizing:border-box;margin:0;padding:0}
html,body{width:1200px;height:2817px;overflow:hidden;background:#fff}
body{position:relative;font-family:"Open Sans",sans-serif;color:var(--ink)}
.abs{position:absolute}

.page-banner{left:0;top:0;width:1200px;height:103px;background:linear-gradient(180deg,#1b47d6 0%,#0b2fa8 60%,#072486 100%)}
.page-banner h1{position:absolute;left:105px;top:32px;font-family:"Oswald",sans-serif;font-weight:600;font-size:34px;color:#fff;letter-spacing:.3px}

.breadcrumb{left:112px;top:137px;font-family:"Roboto",sans-serif;font-size:16px;color:#222}
.breadcrumb span{margin-right:8px}
.breadcrumb .current{color:var(--blue-link)}

.product-card{left:75px;top:188px;width:1039px;height:2315px;border:2px solid #c8c8c8;border-radius:10px}

.fit-note{left:116px;top:201px;width:972px;height:64px;background:var(--panel-bg);border:1.5px solid #b7d4d8;font-family:"Roboto",sans-serif;font-size:20px;line-height:61px;padding-left:18px}

.hero-photo{left:131px;top:291px;width:827px;height:366px;border-radius:6px;background:radial-gradient(ellipse at 45% 40%,#d8d8dc 0%,#b9babf 45%,#fff 75%)}

.thumbs{left:117px;top:669px;display:flex;gap:16px}
.thumb{width:95px;height:90px;border-bottom:4px solid var(--blue);background:linear-gradient(160deg,#8a8f98,#3b4350)}
.thumb:nth-child(2){background:linear-gradient(160deg,#5e8fd4,#1a3f7c)}
.thumb:nth-child(3),.thumb:nth-child(4){background:linear-gradient(160deg,#d6d6d6,#5a5a5a)}

.buy-box{left:798px;top:558px;width:276px;height:477px;border:2px solid #cfcfcf;border-radius:8px;background:#fff}
.price{position:absolute;left:13px;top:14px;font-family:"Oswald",sans-serif;font-weight:600;font-size:29px;color:var(--red)}
.spec{position:absolute;left:24px;width:230px;display:flex;justify-content:space-between;font-size:15.5px}
.spec s{color:#333}
.color-label{position:absolute;left:14px;top:187px;font-size:15.5px;font-weight:600}
.color-label b,.req{color:var(--red)}
.select{position:absolute;border:1.5px solid #9a9a9a;border-radius:3px;background:#fff;font-size:19px;color:#222}
.select::after{content:"";position:absolute;right:12px;top:50%;margin-top:-3px;border:7px solid transparent;border-top:8px solid #888}
.req{position:absolute;left:14px;top:278px;font-size:15.5px}
.qty-label{position:absolute;left:14px;top:317px;font-size:15.5px;color:var(--orange)}
.btn{position:absolute;background:var(--orange);color:#fff;font-family:"Roboto",sans-serif;font-weight:500;font-size:17px;text-align:center;border-radius:6px;box-shadow:0 3px 0 #d9733a}
.ship-badge{position:absolute;left:45px;top:425px;width:190px;height:40px}

.side-box{left:796px;width:278px;border:1.5px solid #c8c8c8;background:#fff}
.side-head{background:var(--blue);color:#fff;font-family:"Roboto",sans-serif;font-weight:500;font-size:17px;height:46px;line-height:46px;padding-left:16px}
.addon{position:absolute;left:796px;width:278px;border:1.5px solid #c8c8c8;background:#fff}
.addon .pic{position:absolute;left:8px;top:12px;width:60px;height:86px;border-radius:4px;background:linear-gradient(180deg,#555,#111)}
.addon h3{position:absolute;left:84px;top:14px;font-family:"Roboto",sans-serif;font-weight:500;font-size:16px;color:var(--blue-link);line-height:20px}
.addon p{position:absolute;left:84px;font-size:14px;line-height:17px;color:#222}
.addon .free{color:var(--red);font-weight:700;left:115px}
.addon .cost{position:absolute;left:84px;font-family:"Oswald",sans-serif;font-weight:500;font-size:25px;color:var(--red)}
.addon .cost i{display:inline-block;width:14px;height:14px;border:1.5px solid #999;border-radius:2px;margin-left:10px;vertical-align:middle;background:#fafafa}

.section{position:absolute;left:115px;width:657px;border:1.5px solid #bfbfbf;border-radius:4px;background:#fff}
.section h2{position:absolute;left:28px;font-family:"Roboto",sans-serif;font-weight:500;font-size:20px;color:#111}
.body-copy{position:absolute;font-size:15.5px;line-height:22.5px;text-align:justify;color:#222}
.sub{position:absolute;left:36px;width:470px;font-family:"Roboto",sans-serif;font-weight:500;font-size:16px;padding-bottom:12px;border-bottom:1px solid #ddd}
.features{position:absolute;left:57px;top:311px;list-style:none;font-family:"Noto Sans",sans-serif;font-size:21px;line-height:35.6px;color:#222}
.more{position:absolute;right:44px;font-size:15px;color:var(--red)}

.review-title{position:absolute;left:28px;top:58px;font-family:"Roboto",sans-serif;font-weight:500;font-size:20px;color:var(--red)}
.reviewer{position:absolute;left:475px;top:55px;font-family:"Roboto",sans-serif;font-size:17px;color:#333}
.avatar{position:absolute;left:563px;top:41px;width:50px;height:50px;border-radius:50%;background:linear-gradient(#8a8a8a,#333)}
.rating-bar{position:absolute;left:28px;top:233px;width:500px;height:64px;background:#e4e4e4;display:flex;align-items:center;padding:0 18px;gap:10px}
.supporters{margin-left:100px;font-family:"Roboto",sans-serif;font-weight:500;font-size:14px;display:flex;align-items:center;gap:8px}

.warranty-head{position:absolute;left:28px;top:58px;font-family:"Roboto",sans-serif;font-weight:500;font-size:18px;color:var(--blue-link)}
.q{position:absolute;left:28px;font-family:"Roboto",sans-serif;font-weight:700;font-size:17px;display:flex;align-items:center;gap:10px;letter-spacing:.1px}
.q i{display:inline-block;width:15px;height:15px;border-radius:50%;position:relative}
.q i::before{content:"";position:absolute;left:3px;right:3px;top:6px;height:3px;background:#fff}
.q i.plus::after{content:"";position:absolute;top:3px;bottom:3px;left:6px;width:3px;background:#fff}

.signup{left:178px;top:2532px}
.signup h2{font-family:"Roboto",sans-serif;font-weight:700;font-size:24px;color:#111}
.signup .pitch{position:absolute;left:0;top:44px;font-size:15.5px;line-height:20px;padding-left:26px;width:460px}
.signup .pitch::before{content:"\201C";position:absolute;left:-26px;top:-6px;font-size:50px;color:#bbb;font-family:Georgia,serif;line-height:1}
.field-row{position:absolute;left:0;display:flex;align-items:center;gap:6px;font-size:15.5px;white-space:nowrap}
.field{height:22px;background:var(--field);border:1px solid #bbb}

.hills{left:0;top:2755px;width:1200px;height:62px;background:linear-gradient(180deg,#fff 0%,#cfdcec 55%,#a4b8d4 100%)}
</style>
</head>
<body>

<header class="page-banner abs"><h1>up to 16’8” Long and 90” Wide</h1></header>

<nav class="breadcrumb abs"><span>Home &gt;</span> <span>Boat Covers &gt;</span> <span>Center Console with Bow Rails &gt;</span> <span class="current">up to 16’8” Long and 90” Wide</span></nav>

<main class="product-card abs"></main>

<div class="fit-note abs">Fits : Center Console with Bow Rails upto 16’8” Long and 90” Wide</div>

<div class="hero-photo abs" role="img" aria-label="Grey boat cover strapped over a center console boat on a trailer"></div>

<div class="thumbs abs">
  <div class="thumb" role="img" aria-label="Cover detail"></div>
  <div class="thumb" role="img" aria-label="Blue cover fabric"></div>
  <div class="thumb" role="img" aria-label="Cover corner"></div>
  <div class="thumb" role="img" aria-label="Strap buckle"></div>
  <div class="thumb" role="img" aria-label="Strap close-up"></div>
  <div class="thumb" role="img" aria-label="Packed straps"></div>
</div>

<aside class="buy-box abs">
  <div class="price">$331.50</div>
  <div class="spec" style="top:66px"><span>Regular Price :</span><s>$ 442.00</s></div>
  <div class="spec" style="top:96px"><span>Your Save :</span><span>$110.50</span></div>
  <div class="spec" style="top:126px"><span>Availability :</span><span>Ready to ship</span></div>
  <div class="spec" style="top:156px"><span>Ships :</span><span>1 Business Day</span></div>
  <div class="color-label"><b>*</b> Color</div>
  <div class="select" style="left:19px;top:221px;width:238px;height:44px;line-height:41px;padding-left:24px">Please Select</div>
  <div class="req">* Required Fields</div>
  <div class="qty-label">Quantity :</div>
  <div class="select" style="left:152px;top:311px;width:105px;height:30px;line-height:27px;padding-left:10px;font-size:16px">1</div>
  <div class="btn" style="left:15px;top:360px;width:246px;height:40px;line-height:40px">ADD TO CART</div>
  <svg class="ship-badge" viewBox="0 0 190 40">
    <polygon points="30,4 186,4 176,20 186,36 30,36" fill="#1340c9"/>
    <circle cx="18" cy="20" r="17" fill="#1340c9"/>
    <circle cx="18" cy="20" r="11" fill="#f7a23a"/>
    <text x="44" y="26" font-family="Roboto,sans-serif" font-weight="700" font-size="17" fill="#fff">Free Shipping*</text>
  </svg>
</aside>

<section class="side-box abs" style="top:1059px;height:48px"><div class="side-head">Frequently Purchased Together</div></section>

<article class="addon" style="top:1106px;height:117px">
  <div class="pic" role="img" aria-label="Support pole" style="background:linear-gradient(90deg,#eee,#777,#eee)"></div>
  <h3>SUPPORT POLE</h3>
  <p style="top:40px">Works for Boats and Trucks</p>
  <div class="cost" style="top:60px">$30.75<i></i></div>
</article>
<article class="addon" style="top:1230px;height:114px">
  <div class="pic" role="img" aria-label="Boat motor cover" style="background:linear-gradient(180deg,#2d3f7a,#0e1a3f)"></div>
  <h3 style="top:10px">BOAT MOTOR COVER</h3>
  <p style="top:32px">Heavy duty waterproof<br>material</p>
  <div class="cost" style="top:66px">$30.75<i></i></div>
</article>
<article class="addon" style="top:1352px;height:120px">
  <div class="pic" role="img" aria-label="Strap and buckle pack"></div>
  <h3 style="top:10px">132 IN. STRAPS AND<br>BUCKLE PACK</h3>
  <p class="free" style="top:54px">FREE !</p>
  <div class="cost" style="top:70px">$30.75<i></i></div>
</article>
<article class="addon" style="top:1480px;height:131px">
  <div class="pic" role="img" aria-label="Storage bag" style="top:20px"></div>
  <h3 style="top:22px">STORAGE BAG</h3>
  <p class="free" style="top:50px">FREE !</p>
  <div class="cost" style="top:78px">$30.75<i></i></div>
</article>

<section class="side-box abs" style="top:1630px;height:295px">
  <div class="side-head">Looking for and indoor Cover ?</div>
  <div role="img" aria-label="Boat under a blue indoor cover" style="position:absolute;left:50px;top:60px;width:170px;height:110px;background:radial-gradient(ellipse at 50% 45%,#2f6fe0 0%,#1a4fb8 40%,#fff 72%)"></div>
  <div style="position:absolute;left:42px;top:180px;font-family:Roboto,sans-serif;font-weight:500;font-size:16px;line-height:22px;color:var(--blue-link)">Harborline 600 denier Boat<br>Cover fits V-Hull Runabout</div>
  <div style="position:absolute;left:38px;top:228px;font-family:Oswald,sans-serif;font-size:21px;color:#222"><s>$ 300.00</s></div>
  <div style="position:absolute;left:42px;top:252px;font-family:Oswald,sans-serif;font-weight:500;font-size:26px;color:var(--red)">$ 138.81</div>
</section>

<section class="section" style="top:815px;height:725px">
  <h2 style="top:30px">Product Info</h2>
  <div class="sub" style="top:90px">Description :</div>
  <p class="body-copy" style="left:36px;top:128px;width:585px">When a Boat is stored outside it is exposed to harmful elements such as wind, dirt, rian, and UV. The Ironclad Supreme is the most powerful cover available providing 10x more strength and protection compared to the competition. The 1200 denier fabric is 100% waterproof and provides excellent protection against sun, rain, wind and snow.</p>
  <div class="sub" style="top:274px">Features :</div>
  <ul class="features">
    <li>5 Star Fit. FIt guaranteed or your money back</li>
    <li>10 Year Warranty. Full warranty covering rips and tears</li>
    <li>The covers comes in Grey, Blue and Maroon</li>
    <li>The Fabric is pure 100% Marine Polyster (No. Cotton mix)</li>
    <li>No worries, the cover is 100% waterproof</li>
    <li>Fully Breathable, you'll never see mold or mildew</li>
    <li>UV resistant an dalso prevents heat buildup</li>
    <li>Fully Trailerable (straps included)</li>
    <li>The Cover also comes with an integrated hen cord to<br>be used when mooring or on boat lifts</li>
    <li>Tough - Strong - Durable</li>
  </ul>
</section>

<section class="section" style="top:1549px;height:329px">
  <h2 style="top:10px">Reviews</h2>
  <div class="review-title">Nunc vestibulum sodales nulla</div>
  <div class="reviewer">Sam Reed</div>
  <div class="avatar" role="img" aria-label="Reviewer avatar"></div>
  <p class="body-copy" style="left:28px;top:100px;width:600px">Lorem ipsum dolor sit amet, consectetur adipisicing elit, sed do eiusmod tempor incididunt ut labore et dolore magna aliqua. Ut enim ad minim veniam, quis nostrud exercitation ullamco laboris nisi ut aliquip ex ea commodo consequat. Duis aute irure dolor in reprehenderit in voluptate velit esse cillum dolore eu fugiat nulla pariatur.</p>
  <div class="rating-bar">
    <svg width="140" height="28" viewBox="0 0 140 28">
      <defs><polygon id="star" points="14,1 17.6,10 27,10.3 19.6,16.2 22.2,25.6 14,20.2 5.8,25.6 8.4,16.2 1,10.3 10.4,10"/>
      <clipPath id="half"><rect x="112" y="0" width="14" height="28"/></clipPath></defs>
      <use href="#star" fill="#1a2f73"/>
      <use href="#star" x="28" fill="#1a2f73"/>
      <use href="#star" x="56" fill="#1a2f73"/>
      <use href="#star" x="84" fill="#1a2f73"/>
      <use href="#star" x="112" fill="none" stroke="#1a2f73" stroke-width="1.5"/>
      <use href="#star" x="112" fill="#1a2f73" clip-path="url(#half)"/>
    </svg>
    <div class="supporters">
      <svg width="24" height="18" viewBox="0 0 24 18" fill="#1a3fc2"><circle cx="12" cy="5" r="4"/><path d="M4 18c0-5 3.5-7 8-7s8 2 8 7z"/><circle cx="4" cy="6" r="3"/><circle cx="20" cy="6" r="3"/><path d="M0 16c0-3 1.5-5 4-5l1 .2C3.5 12.5 3 14 3 16z"/><path d="M24 16c0-3-1.5-5-4-5l-1 .2c1.5 1.3 2 2.8 2 4.8z"/></svg>
      15,583 Supporters
    </div>
    <svg style="margin-left:auto" width="16" height="16" viewBox="0 0 16 16" fill="#333"><circle cx="12" cy="3" r="2.5"/><circle cx="4" cy="8" r="2.5"/><circle cx="12" cy="13" r="2.5"/><path d="M12 3L4 8l8 5" stroke="#333" stroke-width="1.4" fill="none"/></svg>
  </div>
  <div class="more" style="top:297px">more...</div>
</section>

<section class="section" style="top:1887px;height:344px">
  <h2 style="top:10px">Warranty</h2>
  <div class="warranty-head">LIMITED WARRANTY POLICY AND GUIDELINES</div>
  <div class="q" style="top:85px"><i style="background:var(--red)"></i>WHAT IS THE SUMMIT TRAIL® WARRANTY POLICY?</div>
  <p class="body-copy" style="left:57px;top:108px;width:570px">Lorem ipsum dolor sit amet, consectetur adipisicing elit, sed do eiusmod tempor incididunt ut labore et dolore magna aliqua. Ut enim ad minim veniam, quis nostrud exercitation ullamco laboris nisi ut aliquip ex ea commodo consequat. Duis aute irure dolor in reprehenderit in voluptate velit esse cillum dolore eu fugiat nulla pariatur.</p>
  <div class="q" style="top:267px"><i class="plus" style="background:#111"></i>WHAT DOES "LIFETIME" MEAN?</div>
  <div class="q" style="top:289px"><i class="plus" style="background:#111"></i>IS NORMAL WEAR AND TEAR COVERED BY WARRANTY?</div>
  <div class="q" style="top:311px"><i class="plus" style="background:#111"></i>HOW TO SEND MY PRODUCT IN FOR A WARRANTY CLAIM?</div>
</section>

<section class="section" style="top:2240px;height:215px">
  <h2 style="top:10px">Shipping</h2>
  <p class="body-copy" style="left:28px;top:54px;width:600px">Lorem ipsum dolor sit amet, consectetur adipisicing elit, sed do eiusmod tempor incididunt ut labore et dolore magna aliqua. Ut enim ad minim veniam, quis nostrud exercitation ullamco laboris nisi ut aliquip ex ea commodo consequat. Duis aute irure dolor in reprehenderit in voluptate velit esse cillum dolore eu fugiat nulla pariatur.</p>
  <div class="more" style="top:176px">more...</div>
</section>

<section class="signup abs">
  <h2>SIGN ME UP !</h2>
  <p class="pitch">I would like to receive your ebook in my inbox<br>on a regular basis</p>
  <div class="field-row" style="top:96px">First Name <span class="field" style="width:145px"></span> last name <span class="field" style="width:145px;margin-left:4px"></span></div>
  <div class="field-row" style="top:124px">email address : <span class="field" style="width:253px"></span></div>
  <div class="btn" style="left:0;top:163px;width:245px;height:43px;line-height:43px">SUBSCRIBE</div>
</section>

<div class="hills abs" role="img" aria-label="Soft blue mountain range along the bottom edge"></div>

</body>
</html>
```